At Home Pet Euthanasia - business cards & brand stationary

We already have a logo and the colors and a website. Need a business card designed that will be able to customized to multiple veterinarians who will be partnering with us. The feel needs to be compassionate, comforting with our tagline 'A Gift of Love at Home'. It will be 2 sides.
On the back our platform/partner vets will be customizing each business card with their own service areas, phone numbers, name and title. On the front, i would like to see experimentation with use of our photos, the logo, tagline and a description 'Peaceful and Compassionate At-Home Pet Euthanasia'

```html
<!DOCTYPE html>
<html lang="en">
<head>
<meta charset="utf-8">
<title>Gentle Paw – Business Card</title>
<link href="https://fonts.googleapis.com/css2?family=Montserrat:wght@700&family=Questrial&family=Playball&display=swap" rel="stylesheet">
<style>
  :root {
    --page: #d9d9da;
    --brand-blue: #5e87b9;
    --brand-blue-light: #6a93c2;
    --brand-blue-deep: #4f7ab0;
    --white: #ffffff;
    --photo-warm: #d9a08e;
    --photo-cream: #e6e2dc;
    --photo-grey: #a9a7a4;
  }
  * { margin: 0; padding: 0; box-sizing: border-box; }
  html, body {
    width: 1200px; height: 800px; overflow: hidden;
    background: var(--page);
  }
  .sheet {
    width: 1200px; height: 800px;
    display: flex; align-items: center; justify-content: center; gap: 40px;
  }
  .card {
    position: relative;
    width: 560px; height: 320px;
    overflow: hidden;
    box-shadow: 0 10px 24px rgba(0,0,0,0.18);
  }

  /* Back side: contact details */
  .card-back {
    background: linear-gradient(135deg, var(--brand-blue-light), var(--brand-blue-deep));
    color: var(--white);
  }
  .brand-mark {
    position: absolute; top: 26px; right: 30px;
    display: flex; align-items: center; gap: 8px;
    font-family: "Questrial", sans-serif; font-size: 17px;
  }
  .brand-dot {
    width: 14px; height: 14px; border-radius: 50%; background: var(--white);
  }
  .identity {
    position: absolute; left: 0; top: 128px; width: 268px;
    text-align: right;
  }
  .person-name {
    font-family: "Montserrat", sans-serif; font-weight: 700;
    font-size: 21px; letter-spacing: 1px; text-transform: uppercase;
  }
  .person-title {
    font-family: "Questrial", sans-serif; font-size: 15px; margin-top: 2px;
  }
  .divider {
    position: absolute; left: 290px; top: 96px; width: 1px; height: 128px;
    background: var(--white);
  }
  .contact {
    position: absolute; left: 312px; top: 100px;
    font-family: "Questrial", sans-serif; font-size: 13.5px; line-height: 1.35;
  }
  .contact-address { margin-bottom: 12px; }
  .contact-row { display: flex; align-items: center; gap: 8px; }
  .contact-row svg { width: 11px; height: 11px; flex: none; }

  /* Front side: photo with tagline band */
  .card-front { background: var(--photo-cream); }
  .photo-area {
    position: absolute; inset: 0;
    background:
      radial-gradient(ellipse 40% 55% at 62% 45%, var(--photo-cream), transparent 70%),
      radial-gradient(ellipse 45% 60% at 25% 70%, var(--photo-warm), transparent 75%),
      linear-gradient(120deg, var(--photo-grey), var(--photo-cream) 60%, var(--photo-grey));
  }
  .tagline-band {
    position: absolute; left: 0; right: 0; bottom: 34px; height: 44px;
    background: var(--brand-blue-deep);
    display: flex; align-items: center; justify-content: center;
  }
  .tagline {
    font-family: "Playball", cursive; color: var(--white);
    font-size: 25px; letter-spacing: 0.3px;
  }
</style>
</head>
<body>
<main class="sheet">
  <section class="card card-back" aria-label="Business card back">
    <div class="brand-mark"><span class="brand-dot"></span><span class="brand-name">Gentle Paw</span></div>
    <div class="identity">
      <p class="person-name">Daniel Reyes</p>
      <p class="person-title">President</p>
    </div>
    <div class="divider"></div>
    <div class="contact">
      <p class="contact-address">4120 Willow Bend Road<br>Fairbanks, Alaska 99712</p>
      <p class="contact-row">
        <svg viewBox="0 0 12 12" aria-hidden="true"><path fill="#fff" d="M2.5 1 4.5 3 3.6 4.6c.7 1.5 2 2.8 3.8 3.8L9 7.5l2 2-1.3 1.5C5.5 10.6 1.4 6.5 1 2.3Z"/></svg>
        555-014-2273
      </p>
      <p class="contact-row">
        <svg viewBox="0 0 12 12" aria-hidden="true"><rect x="1" y="2.5" width="10" height="7" fill="#fff"/><path d="M1 2.5 6 6.5 11 2.5" fill="none" stroke="#5e87b9" stroke-width="1"/></svg>
        daniel@gentlepaw.com
      </p>
      <p class="contact-row">
        <svg viewBox="0 0 12 12" aria-hidden="true"><circle cx="6" cy="6" r="5" fill="#fff"/><path d="M1 6h10M6 1c-2 3-2 7 0 10M6 1c2 3 2 7 0 10" fill="none" stroke="#5e87b9" stroke-width="0.8"/></svg>
        www.gentlepaw.com
      </p>
    </div>
  </section>

  <section class="card card-front" aria-label="Business card front">
    <div class="photo-area" role="img" aria-label="Photograph of a child hugging a blue-eyed tabby-point cat"></div>
    <div class="tagline-band">
      <p class="tagline">Peaceful &amp; Compassionate At-Home Pet Euthanasia</p>
    </div>
  </section>
</main>
</body>
</html>
```